Varentoria Business Card and Letter Head

We are a leadership assessment consultancy based in Sydney, Australia. We help executive-level decison-makers select leaders for more senior level roles in corporate and government organisations. Our methodology is based on the latest research from the field of neuroscience.
We need a business card design and matching letter head that presents our company, Varentoria, as a:
1. trusted adviser to senior executive-level decison makers
2. niche consultancy who are experts in the field of assessing leadership talent
3. results-focused solution provider who balance scientific methods with pragmatic solutions
The following company details should be used in all designs:
Company Name: Varentoria
Details (for business card):
Derek Hanford
Prime Capacity Officer
Level 29, Marlow Tower
7 Marlow Square
Sydney, NSW 2000 Australia
Phone: 1300 582 714
Mobile: 0412 637 258
Email: derek.hanford@varentoria-example.com.au
Website: varentoria-example.com.au
I have attached the logo for Varentoria (for both a white and black background) - your business card and letter head designs must incoporate this logo and colour scheme.
Thanks for your interest in this project, I'm looking forward to receiving your ideas.
Regards,
Derek
Target Market(s)
Executive-level decison-makers in corporate and government organisations (e.g., CEO, VP, Head of Human Resources)
Industry/Entity Type
Leadership
Look and feel

```html
<!DOCTYPE html>
<html lang="en">
<head>
<meta charset="utf-8">
<title>Varentoria Stationery</title>
<link rel="stylesheet" href="https://fonts.googleapis.com/css2?family=Cabin:wght@400;600&display=swap">
<style>
  :root {
    --brand-red: #bf3021;
    --brand-charcoal: #414042;
    --muted-grey: #8d8d90;
    --paper: #ffffff;
  }
  * { margin: 0; padding: 0; box-sizing: border-box; }
  html, body { width: 848px; height: 1200px; overflow: hidden; background: var(--paper); }
  body { position: relative; font-family: "Cabin", "Gill Sans", sans-serif; }

  .letterhead-band { position: absolute; left: 0; top: 17px; width: 848px; height: 78px; }
  .band-left { position: absolute; left: 0; top: 0; width: 84px; height: 78px; background: var(--brand-red); }
  .band-right { position: absolute; left: 309px; top: 0; width: 539px; height: 78px; }
  .band-right svg { position: absolute; inset: 0; }
  .contact-block {
    position: absolute; left: 14px; top: 9px;
    color: var(--paper); font-size: 11px; line-height: 14px;
  }

  .wordmark { position: absolute; display: flex; align-items: center; gap: 8px; }
  .wordmark-square { width: 16px; height: 16px; background: var(--brand-red); }
  .wordmark-name { color: var(--brand-charcoal); font-weight: 600; font-size: 21px; letter-spacing: -0.3px; }
  .letterhead-wordmark { left: 117px; top: 43px; }

  .card-back { position: absolute; left: 418px; top: 549px; width: 200px; height: 362px; background: var(--paper); }
  .card-back-top { position: absolute; left: 0; top: 0; width: 200px; height: 186px; background: var(--brand-charcoal); }
  .card-back-mid { position: absolute; left: 0; top: 186px; width: 200px; height: 65px; background: var(--brand-red); }
  .card-back-foot { position: absolute; left: 0; top: 319px; width: 200px; height: 43px; background: var(--brand-red); }
  .card-back .wordmark { left: 22px; top: 273px; }

  .card-front {
    position: absolute; left: 410px; top: 931px; width: 363px; height: 201px;
    background: var(--brand-charcoal); border-bottom: 1px solid #222;
  }
  .card-identity {
    position: absolute; right: 96px; top: 9px; text-align: right;
    color: var(--paper); font-size: 14px; line-height: 18px;
  }
  .card-accent { position: absolute; left: 286px; top: 13px; width: 66px; height: 66px; background: var(--brand-red); }
  .card-address, .card-contacts {
    position: absolute; left: 26px; color: var(--muted-grey); font-size: 11px; line-height: 14px;
  }
  .card-address { top: 59px; }
  .card-contacts { top: 113px; }
  .contact-line { display: flex; align-items: center; gap: 4px; }
  .contact-line svg { width: 9px; height: 9px; fill: var(--muted-grey); flex: none; }
</style>
</head>
<body>

<header class="letterhead-band">
  <div class="band-left"></div>
  <div class="wordmark letterhead-wordmark">
    <span class="wordmark-square"></span><span class="wordmark-name">Varentoria</span>
  </div>
  <div class="band-right">
    <svg width="539" height="78" viewBox="0 0 539 78">
      <rect x="0" y="0" width="529" height="78" fill="var(--brand-red)"/>
      <polygon points="328,0 426,0 529,78 381,78" fill="var(--brand-charcoal)"/>
      <polygon points="426,0 539,0 539,78 529,78" fill="var(--brand-red)"/>
    </svg>
    <div class="contact-block">
      <div>Phone: 1300 582 714&nbsp; Mobile: 0412 637 258</div>
      <div>Email: derek.hanford@varentoria-example.com.au</div>
      <div>Website: varentoria-example.com.au</div>
      <div>Level 29, Marlow Tower&nbsp; 7 Marlow Square Sydney, NSW 2000 Australia</div>
    </div>
  </div>
</header>

<section class="card-back">
  <div class="card-back-top"></div>
  <div class="card-back-mid"></div>
  <div class="wordmark">
    <span class="wordmark-square"></span><span class="wordmark-name">Varentoria</span>
  </div>
  <div class="card-back-foot"></div>
</section>

<section class="card-front">
  <div class="card-identity">
    <div>Derek Hanford</div>
    <div>Prime Capacity Officer</div>
  </div>
  <div class="card-accent"></div>
  <div class="card-address">
    <div>Level 29, Marlow Tower</div>
    <div>7 Marlow Square</div>
    <div>Sydney, NSW 2000 Australia</div>
  </div>
  <div class="card-contacts">
    <div class="contact-line">
      <svg viewBox="0 0 10 10"><path d="M1 3 Q1 1 5 1 Q9 1 9 3 L7 4 L6 3 H4 L3 4 Z M2 5 H8 L9 9 H1 Z"/></svg>1300 582 714
    </div>
    <div class="contact-line">
      <svg viewBox="0 0 10 10"><rect x="3" y="0.5" width="4" height="9" rx="0.8"/></svg>0412 637 258
    </div>
    <div class="contact-line">
      <svg viewBox="0 0 10 10"><path d="M1 2 H9 V8 H1 Z M1.5 2.5 L5 5.5 L8.5 2.5" fill="none" stroke="#8d8d90" stroke-width="1"/></svg>derek.hanford@varentoria-example.com.au
    </div>
    <div class="contact-line">
      <svg viewBox="0 0 10 10"><circle cx="5" cy="5" r="4" fill="none" stroke="#8d8d90" stroke-width="1"/><path d="M1 5 H9 M5 1 V9" stroke="#8d8d90" stroke-width="0.8"/></svg>varentoria-example.com.au
    </div>
  </div>
</section>

</body>
</html>
```